Investment company needing business card

We are wanting a business card which looks sharp and easy on the eye. We are thinking of having a business card with the logo embossed on it, to really make it stand out. We will only have a small amount of information of the business card, person's name, position, email address and phone number

Contact Information for Business Card

Danielle Frost
Executive Assistant
+64 21 473 5162
danielf@harwickpartners.co.nz

Requirements
Must have
• Embossed logo
Should not have
• Not to be busy

```html
<!DOCTYPE html>
<html lang="en">
<head>
<meta charset="utf-8">
<title>Harwick Partners – Business Card</title>
<link rel="stylesheet" href="https://fonts.googleapis.com/css2?family=Roboto:wght@400;500&family=Roboto+Condensed:wght@500;700&display=swap">
<style>
  :root {
    --backdrop: #2a2a2a;
    --card: #f1f1f1;
    --brand-green: #22b573;
    --ink-grey: #595959;
    --rule-grey: #bdbdbd;
    --mark-grey: #5f5f5f;
  }
  * { margin: 0; padding: 0; box-sizing: border-box; }
  html, body {
    width: 1200px;
    height: 960px;
    overflow: hidden;
    background: var(--backdrop);
  }
  .business-card {
    position: absolute;
    left: 300px;
    top: 309px;
    width: 600px;
    height: 343px;
    background: var(--card);
    border-radius: 18px;
    overflow: hidden;
  }
  .accent-band {
    position: absolute;
    left: 0;
    bottom: 0;
    width: 100%;
    height: 20px;
    background: var(--brand-green);
    border-top: 2px solid var(--rule-grey);
  }
  .brand {
    position: absolute;
    left: 38px;
    top: 146px;
    height: 48px;
    display: flex;
    align-items: center;
    gap: 10px;
  }
  .brand-square {
    width: 40px;
    height: 40px;
    background: var(--mark-grey);
  }
  .brand-name {
    font-family: "Roboto Condensed", sans-serif;
    font-weight: 700;
    font-size: 24px;
    letter-spacing: 0.5px;
    color: var(--brand-green);
  }
  .divider {
    position: absolute;
    left: 305px;
    top: 113px;
    width: 1px;
    height: 110px;
    background: var(--rule-grey);
  }
  .contact {
    position: absolute;
    left: 332px;
    top: 112px;
    color: var(--ink-grey);
  }
  .person-name {
    font-family: "Roboto Condensed", sans-serif;
    font-weight: 700;
    font-size: 21px;
    line-height: 24px;
    color: var(--brand-green);
    text-transform: uppercase;
  }
  .person-role {
    font-family: "Roboto", sans-serif;
    font-weight: 500;
    font-size: 15px;
    line-height: 20px;
    letter-spacing: 0.3px;
    text-transform: uppercase;
  }
  .details {
    list-style: none;
    margin-top: 10px;
    font-family: "Roboto", sans-serif;
    font-size: 14.5px;
    line-height: 18px;
  }
</style>
</head>
<body>
  <div class="business-card">
    <div class="brand">
      <div class="brand-square"></div>
      <span class="brand-name">HARWICK PARTNERS</span>
    </div>
    <div class="divider"></div>
    <div class="contact">
      <p class="person-name">Danielle Frost</p>
      <p class="person-role">Executive Assistant</p>
      <ul class="details">
        <li>+64 21 473 5162</li>
        <li>danielf@harwickpartners.co.nz</li>
        <li>www.harwickpartners.co.nz</li>
      </ul>
    </div>
    <div class="accent-band"></div>
  </div>
</body>
</html>
```